Im want a website LIKE VRX's and FleetHollow.com's with product payment options like Trenzo's

I need a website LIKE VRX with a header made EXACTLY LIKE THAT OF FLEETHOLLOWS .

The front page photo should be like that of FLEETHOLLOW's webpage as well.

The name of the website will be called "M.K. (Caldera Key)".

We will be targeting ALL MARKETS in a small town in central Panama and charging businesses "listing fees" like a phone book does but also providing informational blogs, news, and other interesting activities.

THIS IS A MULTI PAGE WEBSITE

THIS IS WHERE VRX's website meets Brivelle/FleetHollow.

Once the layout is built I will tweak and modify, add information, and upload items for sale.

Here is a list of specific categories that should be listed out above the front page header image/search bar

-- Home -- News -- Travel -- Activities -- Shop & Dine -- Store -- More... --

These categories should be spread across the bottom of the page in three sections:

WHATS SO GREAT ABOUT (Caldera Key),
HAND PICKED TOURS
ACTIVITIES etc.

Also lets use www.Trenzo.example 's
"HOT DESTINATIONS"
"BEAT THE BEST PRICES IN BOQUETE"
"OCTOBERS INSIDER PICKS"
"TOP DESTINATIONS"
and spread them in four sections side-by-side near the bottom of the page.

Overall I would like to see the finished product to be something LIKE VRX's and FleetHollows.

WE NEED ONLINE PAYMENT OPTIONS LIKE BRIVELLE'S WEBSITE HAS

This will be a desktop website but should be very mobile friendly as well.

-rodmund

P.S. Good luck!

If it isn't already too late to change the website name, the name of the website should be "Caldera Key". Added Friday, October 9, 2015

What do you guys think the budget should be to win this? Added Saturday, October 10, 2015

www.palmorra.example is the most amazing simple site. Whoever can make me a replica with my specifications will win immediately!!!! Added Sunday, October 18, 2015

OMG www.palmorra.example is the bomb!So simple and elegant. Whoever can make me an EXACT REPLICA OF WWW.PALMORRA.EXAMPLE as my site with the specifications mentioned in my brief will take home the $825.00 immediately! Good luck amigos! Added Sunday, October 18, 2015

Does anybody know how to add recurring monthly billing options on this website? Added Sunday, October 18, 2015

ALL MARKETS

Product

Coded - Design and coding required

5+ page

• Coinvey payment options.
• I must be able to add and remove photos/text and video from the HTML files in the page.
• Be creative my friends, and may the odds be forever in your favor!
• I added some photos of a good layout for our page below.

```html
<!DOCTYPE html>
<html lang="en">
<head>
<meta charset="utf-8">
<title>Caldera Key</title>
<link href="https://fonts.googleapis.com/css2?family=Open+Sans:wght@300;400;600;700&display=swap" rel="stylesheet">
<style>
:root{
  --blue:#2b7bcc;
  --blue-dark:#1f64ad;
  --blue-deep:#17528f;
  --heading:#2f86d1;
  --text:#555;
  --muted:#888;
  --page:#ececec;
  --white:#fff;
  --line:#dcdcdc;
  --accent:#f5b23a;
  --price:#333;
  --caption:rgba(18,42,66,.62);
}
*{box-sizing:border-box;margin:0;padding:0}
html,body{width:717px;height:1200px;overflow:hidden}
body{font-family:"Open Sans",Arial,sans-serif;color:var(--text);background:var(--page);position:relative;font-size:9px}
.backdrop{position:absolute;left:0;top:0;width:717px;height:380px;background:
  radial-gradient(ellipse 140px 90px at 20px 30px,rgba(40,110,60,.55),transparent 70%),
  radial-gradient(ellipse 150px 110px at 700px 40px,rgba(40,110,60,.55),transparent 70%),
  radial-gradient(ellipse 260px 60px at 360px 10px,rgba(255,255,255,.55),transparent 70%),
  linear-gradient(180deg,#4fa2e0 0%,#8cc8ec 35%,#cfe9f3 65%,var(--page) 100%)}
.site-title{position:absolute;left:67px;top:12px;color:var(--white);font-size:22px;font-weight:400;letter-spacing:.2px}
.main-nav{position:absolute;left:67px;top:64px;width:583px;height:22px;background:var(--blue);display:flex;align-items:center;padding:0 10px;gap:14px}
.main-nav a{color:var(--white);text-decoration:none;font-size:8.5px;display:flex;align-items:center;gap:3px}
.main-nav a::before{content:"";width:5px;height:5px;border-radius:50%;background:rgba(255,255,255,.75)}
.lang-select{margin-left:auto;width:26px;height:12px;background:var(--white);border-radius:2px;display:flex;align-items:center;justify-content:flex-end;padding-right:3px}
.lang-select span{width:9px;height:6px;background:#d33}
.hero{position:absolute;left:67px;top:94px;width:583px;height:264px;background:
  radial-gradient(ellipse 200px 150px at 470px 90px,rgba(150,130,95,.9),transparent 70%),
  radial-gradient(ellipse 160px 60px at 330px 240px,rgba(30,170,190,.85),transparent 70%),
  radial-gradient(ellipse 120px 80px at 110px 50px,rgba(160,200,230,.8),transparent 70%),
  linear-gradient(160deg,#5aa1d2 0%,#3d86b6 40%,#1f8aa0 70%,#1c4f6e 100%)}
.hero-caption{position:absolute;left:28px;top:72px;width:200px;height:92px;padding:11px 12px;background:var(--caption)}
.hero-caption h2{color:var(--accent);font-size:14px;font-weight:400;margin-bottom:5px;white-space:nowrap}
.hero-caption p{color:var(--white);font-size:7px;line-height:1.4;margin-bottom:8px}
.btn{display:inline-block;background:var(--blue);color:var(--white);font-size:7.5px;padding:4px 9px;border-radius:2px;text-decoration:none}
.hero-dots{position:absolute;left:40px;top:174px;display:flex;gap:5px}
.hero-dots i{width:6px;height:6px;border-radius:50%;background:rgba(255,255,255,.6)}
.hero-dots i:first-child{background:var(--white)}
.panel{position:absolute;left:67px;top:375px;width:583px;height:450px;background:var(--white);padding:14px 16px}
.services{display:flex;gap:20px}
.service{flex:1}
.service .thumb{height:95px}
.service h3{color:var(--heading);font-size:17px;font-weight:400;margin:14px 0 6px}
.service p{font-size:7px;line-height:1.5;color:var(--muted);margin-bottom:10px;height:32px}
.divider{border-top:1px solid var(--line);margin:16px 0 16px}
.section-title{color:var(--heading);font-size:17px;font-weight:400;margin-bottom:12px}
.tours{display:flex;gap:12px}
.tour{flex:1;border:1px solid var(--line);padding:6px}
.tour .thumb{height:66px;margin-bottom:8px}
.tour h4{color:var(--heading);font-size:9px;font-weight:400;line-height:1.3;margin-bottom:6px}
.stars{display:flex;gap:1px;margin-bottom:6px}
.stars svg{width:7px;height:7px;fill:var(--accent)}
.price{display:flex;justify-content:space-between;border-top:1px solid var(--line);padding-top:5px;font-size:7px;color:var(--muted)}
.price b{color:var(--price);font-weight:600}
.info{position:absolute;left:67px;top:842px;width:583px;display:flex;gap:18px}
.info h3{color:var(--heading);font-size:17px;font-weight:400;margin-bottom:10px;white-space:nowrap}
.news{width:195px}
.news-item{display:flex;gap:8px;margin-bottom:10px}
.news-item .thumb{width:52px;height:36px;flex:none}
.news-item p{font-size:7px;line-height:1.45}
.news-item a{color:var(--heading);font-size:7px;text-decoration:none}
.guide{width:160px}
.guide p{font-size:7px;line-height:1.45;margin-bottom:6px}
.guide ul{list-style:none}
.guide li{color:var(--heading);font-size:7.5px;line-height:1.75}
.converter{flex:1}
.field{display:flex;align-items:center;margin-bottom:6px}
.field label{width:42px;font-size:7px}
.field span{flex:1;height:17px;border:1px solid var(--line);background:var(--white);font-size:7px;display:flex;align-items:center;padding-left:6px;gap:5px}
.field span i{width:8px;height:6px;background:#c44}
.footer{position:absolute;left:0;top:1016px;width:717px;height:150px;background:var(--blue);color:var(--white)}
.footer-inner{position:absolute;left:67px;top:14px;width:583px;display:flex}
.footer h4{font-size:11px;font-weight:400;margin-bottom:10px}
.footer p,.footer li{font-size:6.5px;line-height:1.6;color:rgba(255,255,255,.85);list-style:none}
.col-about{width:190px;padding-right:20px}
.col-company,.col-support{width:125px}
.col-social{flex:1}
.social-icons{display:flex;gap:4px}
.social-icons i{width:14px;height:14px;border-radius:50%;background:rgba(255,255,255,.9)}
.mark{position:absolute;left:598px;top:1083px;width:36px;height:36px;border-radius:50%;background:var(--accent)}
.copyright{position:absolute;left:0;top:1166px;width:717px;height:34px;background:var(--blue-deep);color:rgba(255,255,255,.85);font-size:6.5px;display:flex;align-items:center;justify-content:center}
</style>
</head>
<body>
<div class="backdrop" role="img" aria-label="Tropical beach with palm trees under a blue sky"></div>
<h1 class="site-title">Caldera Key</h1>
<nav class="main-nav">
  <a href="#">Hotels</a><a href="#">Flights</a><a href="#">Holiday homes</a><a href="#">Hostels</a><a href="#">Food</a><a href="#">Vehicles</a><a href="#">Video</a><a href="#">Travel ideas</a>
  <div class="lang-select"><span></span></div>
</nav>
<section class="hero" role="img" aria-label="Boat in a turquoise cove beneath rocky cliffs">
  <div class="hero-caption">
    <h2>Tourist Place in Panama</h2>
    <p>Clear coves, quiet beaches and boat trips along the rocky coast await you.</p>
    <a class="btn" href="#">Read More</a>
  </div>
  <div class="hero-dots"><i></i><i></i><i></i></div>
</section>
<main class="panel">
  <div class="services">
    <article class="service">
      <div class="thumb" role="img" aria-label="Woman relaxing on a tropical beach" style="background:radial-gradient(ellipse 60px 30px at 80px 75px,rgba(240,220,180,.9),transparent 70%),linear-gradient(180deg,#4fb5e6 0%,#8fd6ea 45%,#3fc1c9 62%,#ead9b6 80%)"></div>
      <h3>Tours</h3>
      <p>Guided trips to waterfalls, coffee farms and cloud forest trails with local experts who know every path.</p>
      <a class="btn" href="#">Read More</a>
    </article>
    <article class="service">
      <div class="thumb" role="img" aria-label="City skyline with hotel towers by the sea" style="background:linear-gradient(180deg,#3f86cf 0%,#8bbde6 40%,#c7d8e6 55%,#5a84a8 70%,#2c5f8c 100%)"></div>
      <h3>Hotel/Hostels</h3>
      <p>Find rooms for every budget, from small family hostels in town to quiet hotels with mountain views.</p>
      <a class="btn" href="#">Read More</a>
    </article>
    <article class="service">
      <div class="thumb" role="img" aria-label="Harbour with boats and high-rise buildings" style="background:linear-gradient(180deg,#4f9ad8 0%,#a9cfea 45%,#d6dde2 58%,#6d93ad 75%,#3d6f92 100%)"></div>
      <h3>Rental Vehicles</h3>
      <p>Rent cars, scooters and boats from trusted local businesses and explore the region at your own pace.</p>
      <a class="btn" href="#">Read More</a>
    </article>
  </div>
  <div class="divider"></div>
  <h2 class="section-title">Tour &amp; Sightseeing</h2>
  <div class="tours">
    <article class="tour">
      <div class="thumb" role="img" aria-label="Boat cruising on open water" style="background:linear-gradient(180deg,#7fbde8 0%,#4e9ad8 45%,#2f6fa8 100%)"></div>
      <h4>Fishing in Panama City, Florida</h4>
      <div class="stars"><svg viewBox="0 0 10 10"><path d="M5 0l1.5 3.3 3.5.4-2.6 2.4.7 3.5L5 7.8 1.9 9.6l.7-3.5L0 3.7l3.5-.4z"/></svg><svg viewBox="0 0 10 10"><path d="M5 0l1.5 3.3 3.5.4-2.6 2.4.7 3.5L5 7.8 1.9 9.6l.7-3.5L0 3.7l3.5-.4z"/></svg><svg viewBox="0 0 10 10"><path d="M5 0l1.5 3.3 3.5.4-2.6 2.4.7 3.5L5 7.8 1.9 9.6l.7-3.5L0 3.7l3.5-.4z"/></svg><svg viewBox="0 0 10 10"><path d="M5 0l1.5 3.3 3.5.4-2.6 2.4.7 3.5L5 7.8 1.9 9.6l.7-3.5L0 3.7l3.5-.4z"/></svg><svg viewBox="0 0 10 10"><path d="M5 0l1.5 3.3 3.5.4-2.6 2.4.7 3.5L5 7.8 1.9 9.6l.7-3.5L0 3.7l3.5-.4z"/></svg></div>
      <div class="price"><span>From US$</span><b>$79.00</b></div>
    </article>
    <article class="tour">
      <div class="thumb" role="img" aria-label="Bridge over a harbour at dusk" style="background:linear-gradient(180deg,#8aa6d2 0%,#5a7fb4 45%,#2b4f7d 100%)"></div>
      <h4>Fishing in Panama City, Florida</h4>
      <div class="stars"><svg viewBox="0 0 10 10"><path d="M5 0l1.5 3.3 3.5.4-2.6 2.4.7 3.5L5 7.8 1.9 9.6l.7-3.5L0 3.7l3.5-.4z"/></svg><svg viewBox="0 0 10 10"><path d="M5 0l1.5 3.3 3.5.4-2.6 2.4.7 3.5L5 7.8 1.9 9.6l.7-3.5L0 3.7l3.5-.4z"/></svg><svg viewBox="0 0 10 10"><path d="M5 0l1.5 3.3 3.5.4-2.6 2.4.7 3.5L5 7.8 1.9 9.6l.7-3.5L0 3.7l3.5-.4z"/></svg><svg viewBox="0 0 10 10"><path d="M5 0l1.5 3.3 3.5.4-2.6 2.4.7 3.5L5 7.8 1.9 9.6l.7-3.5L0 3.7l3.5-.4z"/></svg><svg viewBox="0 0 10 10"><path d="M5 0l1.5 3.3 3.5.4-2.6 2.4.7 3.5L5 7.8 1.9 9.6l.7-3.5L0 3.7l3.5-.4z"/></svg></div>
      <div class="price"><span>From US$</span><b>$79.00</b></div>
    </article>
    <article class="tour">
      <div class="thumb" role="img" aria-label="Coastline with green hills and sea" style="background:linear-gradient(180deg,#8cc4ea 0%,#5aa2cf 40%,#3f8f9e 65%,#5f8a55 100%)"></div>
      <h4>Fishing in Panama City, Florida</h4>
      <div class="stars"><svg viewBox="0 0 10 10"><path d="M5 0l1.5 3.3 3.5.4-2.6 2.4.7 3.5L5 7.8 1.9 9.6l.7-3.5L0 3.7l3.5-.4z"/></svg><svg viewBox="0 0 10 10"><path d="M5 0l1.5 3.3 3.5.4-2.6 2.4.7 3.5L5 7.8 1.9 9.6l.7-3.5L0 3.7l3.5-.4z"/></svg><svg viewBox="0 0 10 10"><path d="M5 0l1.5 3.3 3.5.4-2.6 2.4.7 3.5L5 7.8 1.9 9.6l.7-3.5L0 3.7l3.5-.4z"/></svg><svg viewBox="0 0 10 10"><path d="M5 0l1.5 3.3 3.5.4-2.6 2.4.7 3.5L5 7.8 1.9 9.6l.7-3.5L0 3.7l3.5-.4z"/></svg><svg viewBox="0 0 10 10"><path d="M5 0l1.5 3.3 3.5.4-2.6 2.4.7 3.5L5 7.8 1.9 9.6l.7-3.5L0 3.7l3.5-.4z"/></svg></div>
      <div class="price"><span>From US$</span><b>$79.00</b></div>
    </article>
    <article class="tour">
      <div class="thumb" role="img" aria-label="Tall towers on a waterfront" style="background:linear-gradient(180deg,#9fcdee 0%,#6e9fc6 50%,#3d6685 100%)"></div>
      <h4>Fishing in Panama City, Florida</h4>
      <div class="stars"><svg viewBox="0 0 10 10"><path d="M5 0l1.5 3.3 3.5.4-2.6 2.4.7 3.5L5 7.8 1.9 9.6l.7-3.5L0 3.7l3.5-.4z"/></svg><svg viewBox="0 0 10 10"><path d="M5 0l1.5 3.3 3.5.4-2.6 2.4.7 3.5L5 7.8 1.9 9.6l.7-3.5L0 3.7l3.5-.4z"/></svg><svg viewBox="0 0 10 10"><path d="M5 0l1.5 3.3 3.5.4-2.6 2.4.7 3.5L5 7.8 1.9 9.6l.7-3.5L0 3.7l3.5-.4z"/></svg><svg viewBox="0 0 10 10"><path d="M5 0l1.5 3.3 3.5.4-2.6 2.4.7 3.5L5 7.8 1.9 9.6l.7-3.5L0 3.7l3.5-.4z"/></svg><svg viewBox="0 0 10 10"><path d="M5 0l1.5 3.3 3.5.4-2.6 2.4.7 3.5L5 7.8 1.9 9.6l.7-3.5L0 3.7l3.5-.4z"/></svg></div>
      <div class="price"><span>From US$</span><b>$79.00</b></div>
    </article>
  </div>
</main>
<section class="info">
  <div class="news">
    <h3>Latest News in Panama</h3>
    <div class="news-item">
      <div class="thumb" role="img" aria-label="Beach scene" style="background:linear-gradient(180deg,#6cb8e6 0%,#9fd6ea 50%,#e6d6b2 100%)"></div>
      <div><p>New coffee trail opens near the river with views of the valley.</p><a href="#">Get Details</a></div>
    </div>
    <div class="news-item">
      <div class="thumb" role="img" aria-label="Harbour scene" style="background:linear-gradient(180deg,#7fb4de 0%,#4f86b8 50%,#2f5f88 100%)"></div>
      <div><p>Local market adds weekend stalls for crafts, food and music.</p><a href="#">Get Details</a></div>
    </div>
  </div>
  <div class="guide">
    <h3>Tours Guide</h3>
    <p>Pick a guide and plan your day with people who live here.</p>
    <ul>
      <li>Volcano sunrise hike</li>
      <li>Hot springs day trip</li>
      <li>River rafting tour</li>
      <li>Coffee farm visit</li>
      <li>Birdwatching walk</li>
    </ul>
  </div>
  <div class="converter">
    <h3>Currency Converter</h3>
    <div class="field"><label>Amount</label><span>100</span></div>
    <div class="field"><label>From</label><span><i></i>US Dollar</span></div>
    <div class="field"><label>To</label><span><i></i>Euro</span></div>
    <a class="btn" href="#">Convert</a>
  </div>
</section>
<footer class="footer">
  <div class="footer-inner">
    <div class="col-about">
      <h4>Caldera Key</h4>
      <p>Your local guide to tours, hotels, food and shops in our small mountain town. Find listings, read news and book trips in one place.</p>
    </div>
    <div class="col-company">
      <h4>Company</h4>
      <ul><li>About Us</li><li>Contact Us</li><li>Media Center</li><li>Careers</li><li>Site Map</li></ul>
    </div>
    <div class="col-support">
      <h4>Support</h4>
      <ul><li>Customer Care</li><li>Privacy Policy</li><li>Listing Fees</li><li>Terms of Use</li><li>Manage Bookings</li></ul>
    </div>
    <div class="col-social">
      <h4>Social</h4>
      <div class="social-icons"><i></i><i></i><i></i><i></i><i></i></div>
    </div>
  </div>
</footer>
<div class="mark"></div>
<div class="copyright">© 2015 Caldera Key. All rights reserved.</div>
</body>
</html>
```